Home Remodeling company needs a business card design

we need a business card design for home remodeling company in hamilton county, indiana USA. we offers a wide range of construction services including whole house renovations, Design and Build Basements and Kitchen and Bathroom Remodeling . we would like to see designs for both site of business card that use the same color of the company logo and also including all information below :
1- Karim Feltous CEO / General Contractor
2- all company contacts Telephone numbers ( 1-888-DULOM-47 ) ( 317-555-0193) email address ( info@dulomhome.com) website ( www.dulomhome.com ) and social media logos (Facebook- twitter- google plus )
3- company logo
4- licensed . insured . bonded

```html
<!DOCTYPE html>
<html lang="en">
<head>
<meta charset="utf-8">
<title>Dulom Home Remodeling – Business Card</title>
<link rel="stylesheet" href="https://fonts.googleapis.com/css2?family=Lato:wght@400;700&display=swap">
<style>
  :root {
    --page-bg: #d9d6d2;
    --card-bg: #eef0f1;
    --roof-dark: #1d1d20;
    --brand-red: #a3141c;
    --text-dark: #1e1e22;
    --text-light: #e4e1dc;
    --accent-soft: #c98d8b;
    --icon-fill: #a8907e;
    --icon-glyph: #f2ede8;
  }
  * { margin: 0; padding: 0; box-sizing: border-box; }
  html, body {
    width: 1200px; height: 969px; overflow: hidden;
    background: var(--page-bg);
    font-family: "Lato", sans-serif;
  }
  .card {
    position: absolute; left: 80px; top: 187px;
    width: 1040px; height: 594px;
    background: var(--card-bg);
    overflow: hidden;
    box-shadow: 0 10px 30px rgba(0,0,0,0.18);
  }
  .roof { position: absolute; inset: 0; width: 100%; height: 100%; }
  .company {
    position: absolute; left: 58px; top: 58px;
    color: var(--text-dark); font-weight: 700;
  }
  .company-name {
    font-size: 64px; letter-spacing: 3px; line-height: 1;
  }
  .company-trade {
    font-size: 22px; letter-spacing: 6.5px; line-height: 1.5;
  }
  .person {
    position: absolute; right: 54px; top: 60px; text-align: right;
  }
  .person-name {
    font-weight: 700; font-size: 40px; letter-spacing: 1px;
    color: var(--text-dark); text-transform: uppercase; line-height: 1.1;
  }
  .person-title {
    font-size: 30px; color: var(--brand-red); line-height: 1.35;
  }
  .contact {
    position: absolute; left: 0; right: 0; top: 368px;
    text-align: center; color: var(--text-light);
    font-size: 26px; line-height: 41px;
  }
  .credentials { color: var(--accent-soft); letter-spacing: 1px; }
  .social {
    position: absolute; left: 0; right: 0; top: 510px;
    display: flex; justify-content: center; gap: 8px;
  }
  .social-icon { width: 44px; height: 44px; }
</style>
</head>
<body>
  <div class="card">
    <svg class="roof" viewBox="0 0 1040 594" aria-hidden="true">
      <polygon points="0,545 520,170 1040,545 1040,594 0,594" fill="var(--roof-dark)"/>
      <polyline points="0,540 520,162 1040,540" fill="none" stroke="var(--brand-red)" stroke-width="7"/>
      <g class="window-icon" fill="var(--icon-fill)">
        <rect x="500" y="276" width="18" height="18"/>
        <rect x="522" y="276" width="18" height="18"/>
        <rect x="500" y="298" width="18" height="18"/>
        <rect x="522" y="298" width="18" height="18"/>
      </g>
    </svg>

    <div class="company">
      <p class="company-name">DULOM</p>
      <p class="company-trade">HOME REMODELING</p>
    </div>

    <div class="person">
      <p class="person-name">Karim Feltous</p>
      <p class="person-title">CEO / General Contractor</p>
    </div>

    <div class="contact">
      <p>1-888-DULOM-47 | 317-555-0193</p>
      <p>info@dulomhome.com | www.dulomhome.com</p>
      <p class="credentials">LICENSED | INSURED | BONDED</p>
    </div>

    <div class="social">
      <svg class="social-icon" viewBox="0 0 44 44" role="img" aria-label="Share">
        <circle cx="22" cy="22" r="22" fill="var(--icon-fill)"/>
        <g fill="var(--icon-glyph)" stroke="var(--icon-glyph)" stroke-width="2">
          <line x1="16" y1="22" x2="28" y2="15"/>
          <line x1="16" y1="22" x2="28" y2="29"/>
          <circle cx="15" cy="22" r="3.5"/>
          <circle cx="29" cy="14" r="3.5"/>
          <circle cx="29" cy="30" r="3.5"/>
        </g>
      </svg>
      <svg class="social-icon" viewBox="0 0 44 44" role="img" aria-label="Message">
        <circle cx="22" cy="22" r="22" fill="var(--icon-fill)"/>
        <path d="M12 14 h20 a2 2 0 0 1 2 2 v10 a2 2 0 0 1 -2 2 h-11 l-6 5 v-5 h-3 a2 2 0 0 1 -2 -2 v-10 a2 2 0 0 1 2 -2 z" fill="var(--icon-glyph)"/>
      </svg>
      <svg class="social-icon" viewBox="0 0 44 44" role="img" aria-label="Website">
        <circle cx="22" cy="22" r="22" fill="var(--icon-fill)"/>
        <g fill="none" stroke="var(--icon-glyph)" stroke-width="2">
          <circle cx="22" cy="22" r="11"/>
          <ellipse cx="22" cy="22" rx="5" ry="11"/>
          <line x1="11" y1="22" x2="33" y2="22"/>
        </g>
      </svg>
    </div>
  </div>
</body>
</html>
```